Business Cards Design for the electrical wholesaler: clean bold dynamic :)

We need a business card design that would follow our latest brand guidelines. As an electrical wholesaler we want to bring a fresh look and feel into the industry. The design should be clean bold and dynamic. It should come alive with the renewed energy of our green colour. Our grey colour should keep things balanced and complement the notion of maturity and responsibility. We employ Lato as a corporate font however are not bound by this font and we’re open to interpretation here.

Target Market(s)

Electrical contractors

Industry/Entity Type

Business

Contact Information for Business Card

Logo
Name & Surname: Halyna Dorosh
Job Title: Director of Marketing
Email: halya.dorosh@quillmail.example
Cell phone: XXX.XXX.XXXX
Address: 20517 - 87 Ave. Edmonton, AB, Canada. T6K 4N8
Business Phone: 780.555.0184
Website: www.brovix.example

Font styles to use
Other font styles liked:
• Lato

Requirements
Must have
• Logo & website
Nice to have
• Brand elements - some of them you may find in the attached Brand Guidelines (e.g. three lines on the background signifying "W")

```html
<!DOCTYPE html>
<html lang="en">
<head>
<meta charset="utf-8">
<title>Brovix Electrical Wholesalers – Business Cards</title>
<link rel="stylesheet" href="https://fonts.googleapis.com/css2?family=Lato:wght@400;700;900&display=swap">
<style>
  :root {
    --stage: #2b2b2b;
    --card-dark: #1b1c1c;
    --card-dark-2: #262727;
    --card-light: #ffffff;
    --green: #8cc63f;
    --grey: #5f6062;
    --text-light: #f2f2f2;
    --text-dark: #3a3b3c;
  }
  * { box-sizing: border-box; margin: 0; padding: 0; }
  html, body {
    width: 1200px; height: 896px; overflow: hidden;
    background: var(--stage);
    font-family: "Lato", Arial, sans-serif;
  }
  .stage {
    position: relative; width: 1200px; height: 896px;
    display: flex; align-items: center; justify-content: center; gap: 50px;
  }
  .card {
    position: relative; width: 525px; height: 300px;
    border-radius: 18px; overflow: hidden;
    box-shadow: 0 14px 30px rgba(0,0,0,.45);
  }
  /* Front */
  .card--front { background: linear-gradient(135deg, var(--card-dark-2), var(--card-dark)); }
  .brand { position: absolute; display: flex; align-items: center; gap: 14px; }
  .brand__dot { width: 34px; height: 34px; border-radius: 50%; background: var(--green); flex: none; }
  .brand__name { font-weight: 900; font-size: 62px; line-height: 1; letter-spacing: -1px; }
  .brand__tag {
    font-size: 10.5px; letter-spacing: 2.6px; font-weight: 700; text-transform: uppercase;
    margin-top: 4px;
  }
  .card--front .brand { left: 120px; top: 100px; }
  .card--front .brand__name,
  .card--front .brand__tag { color: var(--text-light); }
  .front__web {
    position: absolute; right: 34px; bottom: 32px;
    color: var(--text-light); font-size: 14px; letter-spacing: .5px;
  }
  .web-accent { color: var(--green); }

  /* Back */
  .card--back { background: var(--card-light); }
  .back__swoosh { position: absolute; inset: 0; }
  .card--back .brand { left: 26px; top: 118px; gap: 12px; }
  .card--back .brand__dot { width: 28px; height: 28px; }
  .card--back .brand__name { color: var(--grey); font-size: 48px; }
  .card--back .brand__tag { color: var(--grey); font-size: 8.5px; letter-spacing: 1.8px; }
  .person { position: absolute; right: 190px; top: 22px; text-align: right; }
  .person__name { color: var(--green); font-weight: 700; font-size: 20px; white-space: nowrap; }
  .person__role { color: var(--text-dark); font-size: 12px; margin-top: 2px; white-space: nowrap; }
  .contact {
    position: absolute; right: 24px; top: 116px; text-align: right;
    color: var(--text-light); font-size: 12px; line-height: 1.7;
  }
  .contact li { list-style: none; display: flex; justify-content: flex-end; align-items: center; gap: 8px; white-space: nowrap; }
  .contact svg { width: 10px; height: 10px; flex: none; }
  .address {
    position: absolute; left: 290px; top: 214px; font-style: normal;
    color: var(--text-light); font-size: 12px; line-height: 1.55; width: 210px;
  }
</style>
</head>
<body>
<main class="stage">

  <section class="card card--front" aria-label="Card front">
    <div class="brand">
      <span class="brand__dot"></span>
      <div>
        <div class="brand__name">Brovix</div>
        <div class="brand__tag">Electrical Wholesalers</div>
      </div>
    </div>
    <div class="front__web">www.<span class="web-accent">brovix</span>.example</div>
  </section>

  <section class="card card--back" aria-label="Card back">
    <svg class="back__swoosh" viewBox="0 0 525 300" preserveAspectRatio="none" aria-hidden="true">
      <defs>
        <linearGradient id="sheen" x1="0" y1="0" x2="1" y2="1">
          <stop offset="0" stop-color="#2c2d2d"/>
          <stop offset="1" stop-color="#161717"/>
        </linearGradient>
      </defs>
      <path d="M215 300 C 230 170 320 60 455 0 L 525 0 L 525 300 Z" fill="#5f6062"/>
      <path d="M227 300 C 242 172 330 62 463 0 L 525 0 L 525 300 Z" fill="#8cc63f"/>
      <path d="M237 300 C 252 174 338 64 471 0 L 525 0 L 525 300 Z" fill="url(#sheen)"/>
    </svg>

    <div class="brand">
      <span class="brand__dot"></span>
      <div>
        <div class="brand__name">Brovix</div>
        <div class="brand__tag">Electrical Wholesalers</div>
      </div>
    </div>

    <div class="person">
      <div class="person__name">Halyna Dorosh</div>
      <div class="person__role">Director of Marketing</div>
    </div>

    <ul class="contact">
      <li><span>780.555.0184</span>
        <svg viewBox="0 0 10 10"><path d="M2 1 L4 1 L4.6 3 L3.4 3.8 Q4.4 5.8 6.2 6.6 L7 5.4 L9 6 L9 8 Q5 9 2.6 6 Q1 4 2 1Z" fill="#8cc63f"/></svg></li>
      <li><span>halya.dorosh@quillmail.example</span>
        <svg viewBox="0 0 10 10"><rect x="1" y="2.5" width="8" height="5.5" fill="none" stroke="#8cc63f" stroke-width="1"/><path d="M1 2.5 L5 5.6 L9 2.5" fill="none" stroke="#8cc63f" stroke-width="1"/></svg></li>
      <li><span>www.<span class="web-accent">brovix</span>.example</span>
        <svg viewBox="0 0 10 10"><circle cx="5" cy="5" r="4" fill="none" stroke="#8cc63f"/><ellipse cx="5" cy="5" rx="1.8" ry="4" fill="none" stroke="#8cc63f" stroke-width=".8"/><path d="M1 5 H9" stroke="#8cc63f" stroke-width=".8"/></svg></li>
    </ul>

    <address class="address">
      20517 - 87 Ave. Edmonton,<br>AB, Canada. T6K 4N8
    </address>
  </section>

</main>
</body>
</html>
```